Business Card Design (NEW FILES)

ATTENTION: New vector files are available. Please update your design to reflect/use the new (better resolution) logo images.

Seeking a unique and professional business card design for a commercial drone photography/videography business. The layout should feature
the logo (attached) and include the following information:
Owen Tarrick
614-502-7738
www.skylarkreelworks.example
NRD Certified Remote Pilot

Owen Tarrick

```html
<!DOCTYPE html>
<html lang="en">
<head>
<meta charset="utf-8">
<title>Skylark Reelworks – Business Card</title>
<link href="https://fonts.googleapis.com/css2?family=Open+Sans:wght@400;600;700;800&display=swap" rel="stylesheet">
<style>
  :root {
    --backdrop: #232323;
    --card: #ffffff;
    --navy: #1b1c4d;
    --orange: #ec8f52;
    --divider: #8a8a8a;
  }
  * { margin: 0; padding: 0; box-sizing: border-box; }
  html, body {
    width: 1200px; height: 780px; overflow: hidden;
    background: var(--backdrop);
    font-family: "Open Sans", Arial, sans-serif;
  }
  .canvas { position: relative; width: 1200px; height: 780px; }
  .card {
    position: absolute; width: 600px; height: 343px;
    background: var(--card); overflow: hidden;
    box-shadow: 0 10px 24px rgba(0,0,0,.45);
  }
  .card--front { left: 150px; top: 27px; }
  .card--back { left: 450px; top: 410px; }

  .brand { display: flex; align-items: center; gap: 12px; color: var(--navy); font-weight: 600; }
  .brand__dot { border-radius: 50%; background: var(--orange); flex: none; }
  .card--front .brand {
    position: absolute; left: 0; right: 0; top: 0; bottom: 0;
    justify-content: center; font-size: 38px; letter-spacing: .5px;
  }
  .card--front .brand__dot { width: 26px; height: 26px; }

  .card--back .brand {
    position: absolute; left: 30px; top: 112px; font-size: 24px; gap: 10px;
  }
  .card--back .brand__dot { width: 18px; height: 18px; }

  .divider {
    position: absolute; left: 272px; top: 34px; width: 1px; height: 192px;
    background: var(--divider);
  }
  .contact { position: absolute; left: 300px; top: 42px; color: var(--navy); }
  .contact__name { font-size: 30px; font-weight: 800; line-height: 1; }
  .contact__first { color: var(--orange); }
  .contact__role { font-size: 14px; font-weight: 700; margin-top: 4px; }
  .contact__list { list-style: none; margin-top: 16px; }
  .contact__item {
    display: flex; align-items: center; gap: 9px;
    font-size: 14px; line-height: 24px; font-weight: 400;
  }
  .contact__icon { width: 14px; height: 14px; flex: none; }

  .accent-block {
    position: absolute; right: 0; top: 236px; width: 130px; height: 28px;
    background: var(--orange);
  }
  .credential-band {
    position: absolute; left: 0; right: 0; top: 264px; height: 40px;
    background: var(--navy); color: #fff;
    display: flex; align-items: center; padding-left: 150px;
    font-size: 15px; font-weight: 400; letter-spacing: .3px;
  }
</style>
</head>
<body>
<main class="canvas">
  <section class="card card--front" aria-label="Card front">
    <div class="brand"><span class="brand__dot"></span><span>Skylark Reelworks</span></div>
  </section>

  <section class="card card--back" aria-label="Card back">
    <div class="brand"><span class="brand__dot"></span><span>Skylark Reelworks</span></div>
    <div class="divider"></div>
    <div class="contact">
      <p class="contact__name"><span class="contact__first">Owen</span> Tarrick</p>
      <p class="contact__role">Owner</p>
      <ul class="contact__list">
        <li class="contact__item">
          <svg class="contact__icon" viewBox="0 0 24 24" aria-hidden="true"><path fill="var(--orange)" d="M6.6 10.8a15.2 15.2 0 0 0 6.6 6.6l2.2-2.2c.3-.3.7-.4 1-.2 1.1.4 2.3.6 3.6.6.6 0 1 .4 1 1V20c0 .6-.4 1-1 1A17 17 0 0 1 3 4c0-.6.4-1 1-1h3.5c.6 0 1 .4 1 1 0 1.3.2 2.5.6 3.6.1.3 0 .7-.2 1z"/></svg>
          614-502-7738
        </li>
        <li class="contact__item">
          <svg class="contact__icon" viewBox="0 0 24 24" aria-hidden="true"><g fill="none" stroke="var(--orange)" stroke-width="2"><circle cx="12" cy="12" r="9"/><ellipse cx="12" cy="12" rx="4" ry="9"/><path d="M3 12h18"/></g></svg>
          www.skylarkreelworks.example
        </li>
        <li class="contact__item">
          <svg class="contact__icon" viewBox="0 0 24 24" aria-hidden="true"><g fill="none" stroke="var(--orange)" stroke-width="2"><rect x="3" y="6" width="18" height="13" rx="1"/><path d="M3 7l9 7 9-7"/></g></svg>
          info@skylarkreelworks.example
        </li>
      </ul>
    </div>
    <div class="accent-block"></div>
    <div class="credential-band">NRD Certified Remote Pilot, Fully Insured</div>
  </section>
</main>
</body>
</html>
```